Letter and Envelope Design For Harborline Realty

Please design a letter and an envelope incorporating our logo (See Attached). We are also launched a business card contest. Since we want them to match, please feel free to submit a design for both the business card and also the letter design and envelope.

Requirements
Must have
• The envelope, the letter and the business cards must match somehow connecting the designs. We want them to have something that holds them together besides the logo.

```html
<!DOCTYPE html>
<html lang="en">
<head>
<meta charset="utf-8">
<title>Harborline Realty – Stationery</title>
<link href="https://fonts.googleapis.com/css2?family=Montserrat:wght@500;600&family=Quicksand:wght@400;500;600&display=swap" rel="stylesheet">
<style>
:root{
  --navy:#28307d;
  --ink:#3b3b3b;
  --grey:#5a5a5a;
  --paper:#ffffff;
  --backdrop:#e4e4e4;
  --desk:#5c5c5c;
  --sig:#cfd0d8;
}
*{margin:0;padding:0;box-sizing:border-box}
html,body{width:1200px;height:3229px;overflow:hidden}
body{position:relative;background:var(--backdrop);font-family:"Quicksand",sans-serif;color:var(--ink)}
.desk{position:absolute;left:0;top:2364px;width:1200px;height:865px;background:var(--desk)}
.sheet{position:absolute;background:var(--paper);box-shadow:0 3px 6px rgba(0,0,0,.25)}
.footer-band{position:absolute;left:0;bottom:0;width:100%;display:block}

/* wordmark */
.mark{position:absolute;display:flex;align-items:center}
.mark-ring{border:2px solid var(--navy);border-radius:50%;flex:none}
.mark-name{font-family:"Montserrat",sans-serif;font-weight:500;color:var(--navy);letter-spacing:.12em;line-height:1.25;white-space:nowrap}

/* letter */
.letter{left:251px;top:169px;width:652px;height:847px}
.letter .mark{left:35px;top:57px}
.letter .mark-ring{width:60px;height:60px;margin-right:10px}
.letter .mark-name{font-size:17px}
.sender{position:absolute;left:305px;top:62px;font-size:11.5px;line-height:18px}
.sender .label{color:var(--navy);font-weight:600}
.head-rule{position:absolute;left:448px;top:64px;width:1px;height:50px;background:var(--ink)}
.contacts{position:absolute;left:465px;top:62px;font-size:11.5px;line-height:18px;list-style:none}
.contacts li{display:flex;align-items:center;gap:7px}
.contacts svg{width:10px;height:10px;fill:var(--navy)}
.contacts .web{color:var(--navy)}
.recipient{position:absolute;left:36px;top:233px;font-size:13px;line-height:22px}
.recipient .name{color:var(--navy);font-weight:600;font-size:14px}
.recipient .role{margin-bottom:6px}
.date{position:absolute;right:37px;top:233px;font-size:13px;font-weight:500}
.body{position:absolute;left:36px;top:343px;width:580px;font-size:12px;line-height:22px;text-align:justify}
.body p+p{margin-top:22px}
.body .cont{margin-top:0}
.closing{position:absolute;left:36px;top:630px;font-size:11px}
.signature{position:absolute;left:36px;top:652px;width:92px;height:34px;background:var(--sig);border-radius:3px}
.signer{position:absolute;left:36px;top:694px;font-size:12px}

/* envelopes */
.env-front{left:80px;top:1216px;width:508px;height:226px}
.env-front .mark{left:30px;top:30px}
.env-front .mark-ring{width:40px;height:40px;margin-right:7px}
.env-front .mark-name{font-size:11.5px}
.return{position:absolute;left:30px;top:155px;padding-left:9px;border-left:1px solid var(--navy);font-size:8.5px;line-height:13px}
.return .label{color:var(--navy);font-weight:600}
.env-back{left:614px;top:1216px;width:508px;height:226px}
.flap{position:absolute;left:0;top:0;display:block}

.pocket-back{left:132px;top:1566px;width:451px;height:637px}
.pocket-front{left:616px;top:1566px;width:452px;height:637px}
.pocket-front .mark{left:27px;top:37px}
.pocket-front .mark-ring{width:36px;height:36px;margin-right:6px}
.pocket-front .mark-name{font-size:10.5px}
.pocket-front .return{left:27px;top:578px;font-size:8px;line-height:12px}

/* business cards */
.card{width:500px;height:286px;top:2650px}
.card-front{left:70px}
.card-front .mark{left:0;top:0;width:100%;height:100%;flex-direction:column;justify-content:center}
.card-front .mark-ring{width:88px;height:88px;margin-bottom:18px;border-width:3px}
.card-front .mark-name{font-size:25px;text-align:center}
.card-back{left:630px}
.card-back .mark{left:34px;top:104px;flex-direction:column;align-items:center}
.card-back .mark-ring{width:64px;height:64px;margin-bottom:12px;border-width:3px}
.card-back .mark-name{font-size:16px;text-align:center}
.card-rule{position:absolute;left:262px;top:62px;width:1px;height:150px;background:var(--grey)}
.card-details{position:absolute;left:276px;top:64px;font-size:11px;line-height:17px;color:var(--grey)}
.card-details .name{font-family:"Montserrat",sans-serif;font-weight:600;font-size:17px;color:var(--navy);line-height:22px}
.card-details .contacts{position:static;margin-top:4px;font-size:11px;line-height:17px}
</style>
</head>
<body>
<div class="desk"></div>

<!-- Letterhead -->
<section class="sheet letter">
  <div class="mark"><span class="mark-ring"></span><span class="mark-name">HARBORLINE<br>REALTY</span></div>
  <div class="sender"><div class="label">Harborline</div>418 Bayview Ave. Ste 210<br>Portsmouth, VA 23701</div>
  <div class="head-rule"></div>
  <ul class="contacts">
    <li><svg viewBox="0 0 10 10"><path d="M2 0l2 2-1 1.5a6 6 0 0 0 3.5 3.5L8 6l2 2-1.5 2C4 10 0 6 0 1.5z"/></svg>+1 555 204 3318</li>
    <li><svg viewBox="0 0 10 10"><path d="M0 2h10v6H0zm1 1v.3l4 2.5 4-2.5V3zm0 1.5V7h8V4.5L5 7z"/></svg>info@harborlinerealty.com</li>
    <li class="web"><svg viewBox="0 0 10 10"><circle cx="5" cy="5" r="5"/></svg>www.harborlinerealty.com</li>
  </ul>
  <div class="recipient"><div class="name">Daniel Whitford</div><div class="role">Manager</div>14 Quai Marin<br>44000 Nantes</div>
  <div class="date">Date: 12/11/2018</div>
  <div class="body">
    <p>Lorem ipsum dolor sit amet, consectetuer adipiscing elit, sed diam nonummy nibh euismod tincidunt ut laoreet dolore magna aliquam erat volutpat. Ut wisi enim ad minim veniam, quis nostrud exerci tation ullamcorper suscipit lobortis nisl ut aliquip ex ea commodo consequat. Lorem ipsum dolor sit amet, cons ectetuer adipiscing elit, sed diam nonummy nibh euismod tincidunt ut laoreet dolore magna aliquam erat volutpat. Ut wisi enim ad minim veniam,</p>
    <p>quis nostrud exerci tation ullamcorper suscipit lobortis nisl ut aliquip ex ea commodo consequat. Lorem ipsum dolor sit amet, consectetuer adipiscing elit, sed diam nonummy nibh euismod tincidunt ut laoreet dolore magna aliquam erat volutpat. Ut wisi enim ad minim veniam,</p>
    <p class="cont">consequat. Duis autem vel eum iriure dolor in hendrerit in vulputate velit esse molestie consequat, vel illum dolore eu feugiat nulla facilisis at vero eros et accumsan .</p>
  </div>
  <div class="closing">sincerely</div>
  <div class="signature" role="img" aria-label="Handwritten signature"></div>
  <div class="signer">Daniel Whitford</div>
  <svg class="footer-band" width="652" height="10" viewBox="0 0 652 10" preserveAspectRatio="none"><polygon points="0,0 330,0 322,10 0,10" fill="#28307d"/><polygon points="334,0 652,0 652,10 326,10" fill="#5a5a5a"/></svg>
</section>

<!-- Envelope front -->
<section class="sheet env-front">
  <div class="mark"><span class="mark-ring"></span><span class="mark-name">HARBORLINE<br>REALTY</span></div>
  <div class="return"><div class="label">Harborline</div>418 Bayview Ave. Ste 210<br>Portsmouth, VA 23701</div>
  <svg class="footer-band" width="508" height="7" viewBox="0 0 508 7" preserveAspectRatio="none"><polygon points="0,0 258,0 252,7 0,7" fill="#28307d"/><polygon points="262,0 508,0 508,7 256,7" fill="#5a5a5a"/></svg>
</section>

<!-- Envelope back -->
<section class="sheet env-back">
  <svg class="flap" width="508" height="95" viewBox="0 0 508 95"><path d="M0 0H508L498 60Q496 70 484 72L262 93Q254 94 246 93L24 72Q12 70 10 60Z" fill="#28307d"/></svg>
</section>

<!-- Pocket envelope back -->
<section class="sheet pocket-back">
  <svg class="flap" width="451" height="74" viewBox="0 0 451 74"><polygon points="0,0 451,0 444,74 7,74" fill="#28307d"/></svg>
</section>

<!-- Pocket envelope front -->
<section class="sheet pocket-front">
  <div class="mark"><span class="mark-ring"></span><span class="mark-name">HARBORLINE<br>REALTY</span></div>
  <div class="return"><div class="label">Harborline</div>418 Bayview Ave. Ste 210<br>Portsmouth, VA 23701</div>
  <svg class="footer-band" width="452" height="7" viewBox="0 0 452 7" preserveAspectRatio="none"><polygon points="0,0 232,0 226,7 0,7" fill="#28307d"/><polygon points="236,0 452,0 452,7 230,7" fill="#5a5a5a"/></svg>
</section>

<!-- Business card front -->
<section class="sheet card card-front">
  <div class="mark"><span class="mark-ring"></span><span class="mark-name">HARBORLINE<br>REALTY</span></div>
</section>

<!-- Business card back -->
<section class="sheet card card-back">
  <div class="mark"><span class="mark-ring"></span><span class="mark-name">HARBORLINE<br>REALTY</span></div>
  <div class="card-rule"></div>
  <div class="card-details">
    <div class="name">DANIEL WHITFORD</div>
    Resident Manager<br>418 Bayview Ave. Ste 210<br>Portsmouth, VA 23701
    <ul class="contacts">
      <li><svg viewBox="0 0 10 10"><path d="M2 0l2 2-1 1.5a6 6 0 0 0 3.5 3.5L8 6l2 2-1.5 2C4 10 0 6 0 1.5z"/></svg>+1 555 204 3318</li>
      <li><svg viewBox="0 0 10 10"><path d="M0 2h10v6H0zm1 1v.3l4 2.5 4-2.5V3zm0 1.5V7h8V4.5L5 7z"/></svg>info@harborlinerealty.com</li>
      <li class="web"><svg viewBox="0 0 10 10"><circle cx="5" cy="5" r="5"/></svg>www.harborlinerealty.com</li>
    </ul>
  </div>
  <svg class="footer-band" width="500" height="8" viewBox="0 0 500 8" preserveAspectRatio="none"><polygon points="0,0 300,0 294,8 0,8" fill="#28307d"/><polygon points="304,0 500,0 500,8 298,8" fill="#5a5a5a"/></svg>
</section>
</body>
</html>
```